A 'new law' boutique Australian law firm that provides specialist employment law and people managem

We value helping clients create results with respect workplaces. What differentiates us is we provide actionable training in understanding and dealing with people and ensure legal compliance fits with this approach. We would like a fresh approach to our training overview documents that we currently use in our current law firm (6 attached). Please use pictures, symbols etc consistent with our non-traditional law approach that captures the approach of each training session.. Attached is the logo and draft letterhead for Birchwell Legal which will launch soon.

Target Market(s)

HR Managers and in-house lawyers (non employment specialists) in mid-large Australian companies that are progressive with a relationship based approach to managing employee behaviours and disputes.

Industry/Entity Type

Human Resource

Font styles to use
Sans Serif

Colors
3176b5
33a6d7

Requirements
Must have
• 1 or 2 page PDF for each of the 6 documents that the wording supplied goes into your design which will be pretty similar as we want consistency with our documents

```html
<!DOCTYPE html>
<html lang="en">
<head>
<meta charset="utf-8">
<title>Managing Conflict and Complaints (Conduct) – Birchwell Legal</title>
<link href="https://fonts.googleapis.com/css2?family=Bitter:wght@400;500;600&display=swap" rel="stylesheet">
<style>
  :root{
    --brand-blue:#3176b5;
    --brand-cyan:#33a6d7;
    --sky:#4cc0ee;
    --sky-mid:#7dd0f0;
    --sky-pale:#d9eff9;
    --ink:#333333;
    --ink-dark:#2b2a2c;
    --white:#ffffff;
    --heading-blue:#1d6fb3;
    --ring-grey:#8c8c8c;
  }
  *{box-sizing:border-box;margin:0;padding:0}
  html,body{width:848px;height:1200px;overflow:hidden;background:var(--white)}
  body{font-family:"Bitter",serif;color:var(--ink);position:relative}
  .sheet{position:relative;width:848px;height:1200px;overflow:hidden}

  /* Header */
  .header-band{position:absolute;left:0;top:0;width:504px;height:117px;background:var(--brand-blue);
    clip-path:polygon(175px 0,504px 0,504px 117px,240px 117px)}
  .brand{position:absolute;left:36px;top:40px;display:flex;align-items:center;gap:10px;z-index:2}
  .brand-dot{width:26px;height:26px;border-radius:50%;background:var(--brand-blue);flex:none}
  .brand-name{font-size:23px;font-weight:500;line-height:27px;color:var(--brand-blue);letter-spacing:.5px;text-transform:uppercase}
  .contact{position:absolute;left:304px;top:66px;color:var(--white);font-size:12.5px;line-height:20px;list-style:none}
  .contact li{display:flex;align-items:center;gap:7px}
  .contact svg{width:13px;height:13px}

  /* Dark intro panel */
  .intro{position:absolute;left:0;top:131px;width:504px;height:692px;background:var(--ink-dark);
    clip-path:polygon(0 0,469px 0,504px 44px,504px 692px,38px 692px,0 643px)}
  .title{position:absolute;right:392px;top:196px;text-align:right;color:var(--white);font-size:37.5px;font-weight:600;line-height:43px;white-space:nowrap}
  .title .accent{color:var(--brand-cyan)}
  .intro-heading{position:absolute;right:392px;top:344px;color:var(--brand-cyan);font-size:20.5px;font-weight:500}
  .intro-copy{position:absolute;left:60px;top:379px;width:396px;text-align:right;color:var(--white);font-size:12.7px;line-height:17px}
  .intro-copy p+p{margin-top:5px}

  .badge{position:absolute;left:82px;top:755px;width:136px;height:136px;border-radius:50%;background:var(--white);
    display:flex;align-items:center;justify-content:center}
  .badge-ring{width:114px;height:114px;border-radius:50%;background:var(--ring-grey);display:flex;align-items:center;justify-content:center}
  .badge-icon{width:100px;height:100px;border-radius:50%;background:var(--brand-cyan)}

  /* Learning outcomes */
  .outcomes{position:absolute;left:60px;top:892px;width:400px}
  .outcomes h2{color:var(--brand-blue);font-size:20.5px;font-weight:500;margin-bottom:9px}
  .outcomes .lead{font-size:12px;line-height:16.5px;font-weight:500;margin-bottom:4px}
  .outcomes ol{font-size:12px;line-height:15.7px;list-style:none}
  .outcomes li{margin-bottom:4px}
  .outcomes li span{display:block;padding-left:12px;text-indent:-12px}

  /* Right column */
  .side{position:absolute;left:504px;top:0;width:344px;height:1200px}
  .block{position:absolute;left:0;width:344px;padding:0 36px 0 41px}
  .block h3{font-size:16.5px;font-weight:500;line-height:21.5px;color:var(--ink)}
  .block ul{list-style:none;font-size:12.3px;line-height:17px;margin-top:8px}
  .block li{padding-left:8px;text-indent:-8px;margin-bottom:4.5px}
  .block li::before{content:"•";margin-right:3px}
  .block-overview{top:0;height:363px;background:var(--sky);color:var(--white);padding-top:24px;
    clip-path:polygon(0 0,344px 0,344px 363px,46px 363px,0 318px)}
  .overview-label{font-size:20.5px;font-weight:500;color:var(--heading-blue);margin-bottom:6px}
  .block-causes{top:363px;height:223px;background:var(--sky-mid);color:var(--white);padding-top:9px}
  .block-approach{top:586px;height:504px;background:var(--sky-pale);padding-top:8px}
  .block-approach h3+h3{margin-top:9px}
  .block-approach ul{color:var(--ink)}
  .key{color:var(--brand-cyan)}
  .block-examples{top:1090px;height:110px;background:var(--sky);color:var(--white);padding-top:8px}
  .block-examples ul{line-height:19px}
  .corner-cut{position:absolute;left:0;width:344px;background:var(--white)}
  .cut-top{top:318px;height:45px;clip-path:polygon(0 0,46px 45px,0 45px);background:var(--sky-mid)}
  .cut-bottom{top:1045px;height:45px;clip-path:polygon(0 0,0 45px,46px 45px);background:var(--sky)}
</style>
</head>
<body>
<main class="sheet">
  <header>
    <div class="header-band"></div>
    <div class="brand"><span class="brand-dot"></span><span class="brand-name">Birchwell<br>Legal</span></div>
    <ul class="contact">
      <li><svg viewBox="0 0 14 14"><circle cx="7" cy="7" r="6" fill="none" stroke="#fff" stroke-width="1.3"/><path d="M1 7h12M7 1c-3 3-3 9 0 12M7 1c3 3 3 9 0 12" fill="none" stroke="#fff" stroke-width="1"/></svg>www.birchwelllegal.com.au</li>
      <li><svg viewBox="0 0 14 14"><circle cx="7" cy="7" r="7" fill="#fff"/><rect x="3.2" y="4.5" width="7.6" height="5" fill="none" stroke="#3176b5" stroke-width="1"/><path d="M3.2 4.5 7 7.5l3.8-3" fill="none" stroke="#3176b5" stroke-width="1"/></svg>info@birchwelllegal.com.au</li>
    </ul>
  </header>

  <section class="intro" aria-label="Training need"></section>
  <h1 class="title">Managing Conflict<br>and Complaints<br><span class="accent">(Conduct)</span></h1>
  <h2 class="intro-heading">Training Need</h2>
  <div class="intro-copy">
    <p>If your job requires you to deal with workplace conflict, then you really care about one thing: having a safe workplace where any conflict can be resolved at the lowest possible level. That initial judgment call and small window to resolve can be the difference between quickly putting out ‘spot fires’ or a ‘major inferno’ that costs thousands, involves lawyers and major collateral damage. It can even cost Managers involved in a bad process their jobs.</p>
    <p>Often it arises out of unresolved performance or behavioural issues that eventually ‘spills over’ into conflict or escalates into complaints. Too often Managers don’t know how to resolve conflict and don’t act until it is too late and then apply common approaches that are legalistic and ineffective.</p>
    <p>This training enables Managers to be more self-reliant in effectively managing employee behaviours and HR better placed to get the right outcomes. It does so by focusing on a practical 3 step approach to dealing with workplace issues to effectively manage a range of behavioural issues arising out of conflict including poor performance, allegations of bullying, and mental health issues.</p>
    <p>In doing so, Managers can resolve workplace conflict and behavioural issues with less time, trouble and expense than formal investigations and deal with the real workplace issues without fear of legal claims.</p>
  </div>

  <div class="badge"><div class="badge-ring"><div class="badge-icon" role="img" aria-label="Icon of two people meeting to resolve conflict"></div></div></div>

  <section class="outcomes">
    <h2>Learning Outcomes</h2>
    <p class="lead">Training utilises learnings from recent case law, case studies, and activities to apply the tools taught, to enable HR to assist managers to:</p>
    <ol>
      <li><span>1. understand how conflict is commonly ‘labelled’ in the workplace and the legal framework in which this operates and how to reframe conflict to avoid the pitfalls of ‘bullying’ being the ‘go to’ labelling of most conflict;</span></li>
      <li><span>2. ‘triage’ to identify likely causes of conflict and complaints to confidently address the real issues through a performance, disciplinary or fitness for work framework (or combination);</span></li>
      <li><span>3. use the performance framework to manage most behavioural issues and understand why this leads to better outcomes;</span></li>
      <li><span>4. use meetings and emails to effectively ‘build your case’ and avoid legal claims without separate legal or complex processes; and</span></li>
      <li><span>5. implement the right process to decide facts and determine outcomes using reasonable response action options.</span></li>
    </ol>
  </section>

  <aside class="side">
    <section class="block block-overview">
      <p class="overview-label">Training Overview</p>
      <h3>Understanding how we label workplace conflict and the relevant legal framework</h3>
      <ul>
        <li>What bullying is and isn’t and distinguishing other unlawful behaviours including discrimination, adverse action, sexual harassment and victimisation</li>
        <li>What is inappropriate behaviour versus appropriate behaviour</li>
        <li>What is and isn’t reasonable management action</li>
        <li>Commonly arising legal claims such as unfair dismissal, adverse action, discrimination, bullying and stress claims</li>
        <li>Individual legal liability for Managers and HR</li>
      </ul>
    </section>
    <div class="corner-cut cut-top"></div>
    <section class="block block-causes">
      <h3>How to identify common causes of conflict and problems with the common approach to resolution</h3>
      <ul>
        <li>4 common Managerial styles and typical conflict</li>
        <li>Change resistance, expectation gaps and perceptions of performance</li>
        <li>What is and isn’t a complaint and the need for early intervention</li>
      </ul>
    </section>
    <section class="block block-approach">
      <h3>3 Step approach to dealing with workplace conflict and complaints: Assess Risk, Determine Facts and Decide Outcomes</h3>
      <h3>Using a Response Action Plan to implement the 3 Step approach</h3>
      <ul>
        <li><span class="key">WH&amp;S Approach</span> to resolving conflict and complaints by assessing relevant risk</li>
        <li>Classifying behaviours and issues into a legal framework of Performance, Conduct (Disciplinary) and Capacity (Fitness for Work) or a combination and the differences</li>
        <li><span class="key">Performance</span> – how to frame performance issues with low intensity (e.g. different types of feedback) through to high intensity (e.g. ‘show cause’ letters) response action</li>
        <li><span class="key">Conduct</span> – how to conduct a disciplinary process with procedural fairness and how to draft effective warning letters as response action</li>
        <li><span class="key">Capacity (Fitness for Work)</span> – how to conduct a fitness for work process and maintain inherent requirements and provide reasonable adjustments as response action</li>
      </ul>
    </section>
    <div class="corner-cut cut-bottom"></div>
    <section class="block block-examples">
      <h3>Examples of scenarios</h3>
      <ul>
        <li>Practice by applying the 3 steps to actual previous issues dealt with and considering different outcomes</li>
      </ul>
    </section>
  </aside>
</main>
</body>
</html>
```